Landscape design build company door flyer

I would like this flyer to convey a high-level of professionalism for a company that is excellent with communication with their clients as well as a company that does incredible installations

Went on vacation/holiday

```html
<!DOCTYPE html>
<html lang="en">
<head>
<meta charset="utf-8">
<title>Summit Stone Builders – Outdoor Living Flyer</title>
<link href="https://fonts.googleapis.com/css2?family=Montserrat:wght@400;500;600;700;800;900&display=swap" rel="stylesheet">
<style>
  :root{
    --navy:#0d2b44;
    --navy-deep:#0a2438;
    --gold:#f9b115;
    --white:#ffffff;
    --paper-grey:#f1f1f1;
    --steel:#8d99a6;
    --photo-wood:#8a4a2c;
    --photo-green:#4d7a3a;
    --photo-stone:#6b6f72;
    --photo-sky:#3a6fc4;
  }
  *{box-sizing:border-box;margin:0;padding:0}
  html,body{width:953px;height:1200px;overflow:hidden;background:var(--white)}
  body{font-family:"Montserrat",sans-serif;position:relative}
  .flyer{position:relative;width:953px;height:1200px;overflow:hidden;background:var(--white)}

  .hero-band{position:absolute;left:0;top:0;width:953px;height:843px}
  .brand{position:absolute;left:357px;top:0;width:229px;height:164px;
    display:flex;flex-direction:column;align-items:center;justify-content:flex-end;padding-bottom:22px}
  .brand-mark{display:block;width:16px;height:16px;background:var(--navy);margin-bottom:12px}
  .brand-name{font-weight:800;font-size:13px;letter-spacing:.2px;color:var(--navy);
    line-height:1.1;white-space:nowrap;text-align:center}

  .headline{position:absolute;left:0;top:204px;width:953px;text-align:center;
    font-weight:900;font-size:51px;line-height:56px;color:var(--white);text-transform:uppercase;letter-spacing:-.5px}
  .headline .accent{color:var(--gold)}

  .about{position:absolute;left:73px;top:423px;width:331px;color:var(--white)}
  .about h2{font-weight:600;font-size:19px;margin-left:2px;margin-bottom:8px;letter-spacing:.2px}
  .about p{font-size:13.3px;line-height:18.2px;text-align:justify;hyphens:auto;-webkit-hyphens:auto;margin-bottom:18px;font-weight:500}

  .photo{position:absolute}
  .photo-deck{left:451px;top:432px;width:160px;height:150px;background:linear-gradient(180deg,var(--photo-green) 0%,#6e8d3f 35%,var(--photo-wood) 55%,#6a3219 100%)}
  .photo-kitchen{left:624px;top:432px;width:255px;height:150px;background:linear-gradient(180deg,#7a4a2a 0%,#3c3a38 35%,var(--photo-stone) 70%,#46484b 100%)}
  .photo-pool{left:451px;top:594px;width:160px;height:109px;background:linear-gradient(180deg,#c9cfc8 0%,#e9ecea 40%,#3fa59a 70%,#1d7f7a 100%)}
  .photo-steps{left:451px;top:715px;width:160px;height:109px;background:linear-gradient(180deg,#4c5a2a 0%,#7a5a3c 30%,#8c8f90 55%,#5b5e61 100%)}
  .photo-firepit{left:624px;top:594px;width:255px;height:230px;background:linear-gradient(180deg,var(--photo-sky) 0%,#6f96d2 35%,#1f2a44 50%,#4b3a30 75%,#8a7766 100%)}

  .services{position:absolute;left:0;top:843px;width:953px;height:207px;
    background:linear-gradient(90deg,var(--white) 0%,var(--white) 52%,#d4d8dc 72%,#5f6f7e 100%)}
  .services h2{position:absolute;left:73px;top:16px;font-weight:700;font-size:21px;color:var(--navy)}
  .service{position:absolute;display:flex;align-items:center;gap:12px;
    font-weight:700;font-size:13.2px;color:var(--navy);white-space:nowrap}
  .service svg{width:32px;height:32px;flex:none}
  .seal{position:absolute;left:737px;top:40px;width:142px;height:142px;border-radius:50%;
    background:radial-gradient(circle,#2a2a2a 0 58%,#c99a1c 59% 100%);border:4px solid #e6c04a}

  .contact{position:absolute;left:0;top:1050px;width:953px;height:150px;background:var(--navy)}
  .contact h3{position:absolute;left:75px;top:20px;font-weight:700;font-size:17px;color:var(--white)}
  .phone{position:absolute;left:72px;top:52px;display:flex;align-items:center;gap:14px;
    font-weight:700;font-size:45px;color:var(--gold);letter-spacing:-.5px;white-space:nowrap}
  .phone svg{width:46px;height:46px}
  .email{position:absolute;left:662px;top:64px;font-size:15.5px;font-weight:400;color:var(--white);letter-spacing:.2px;white-space:nowrap}
</style>
</head>
<body>
<div class="flyer">
  <svg class="hero-band" viewBox="0 0 953 843" aria-hidden="true">
    <defs>
      <linearGradient id="navyFade" x1="0" y1="0" x2="1" y2="1">
        <stop offset="0" stop-color="#123250"/>
        <stop offset="1" stop-color="#0b2741"/>
      </linearGradient>
    </defs>
    <rect x="280" y="0" width="385" height="60" fill="var(--paper-grey)"/>
    <polygon points="0,60 280,60 357,164 586,164 665,60 953,60 953,843 0,843" fill="url(#navyFade)"/>
    <rect x="357" y="0" width="229" height="164" fill="var(--white)"/>
    <line x1="357" y1="164" x2="357" y2="206" stroke="#000" stroke-width="1"/>
    <line x1="586" y1="164" x2="586" y2="206" stroke="#000" stroke-width="1"/>
  </svg>

  <div class="brand">
    <span class="brand-mark"></span>
    <div class="brand-name">SUMMIT STONE BUILDERS</div>
  </div>

  <h1 class="headline">Let’s Create<br><span class="accent">Your Dream Outdoor</span><br>Living Space!</h1>

  <section class="about">
    <h2>ABOUT US</h2>
    <p>Discover the endless possibilities for your outdoor space with The Summit Stone Builders Team. Our team of skilled artisans is dedicated to turning your outdoor space into a breathtaking oasis that you’ll love coming home to. Whether it’s a cozy patio for intimate gatherings, a sprawling deck to host memorable parties, or a custom paver driveway that adds instant curb appeal, our high-quality craftsmanship ensures stunning results that exceed your expectations.</p>
    <p>From concept to completion, we take pride in every detail, using the finest materials to withstand Seattle’s climate while adding timeless elegance to your property. Embrace the Pacific Northwest lifestyle and create cherished moments with family and friends in a captivating outdoor haven.</p>
  </section>

  <div class="photo photo-deck" role="img" aria-label="Wooden deck with pergola and patio chairs among trees"></div>
  <div class="photo photo-kitchen" role="img" aria-label="Covered outdoor kitchen with stacked stone fireplace"></div>
  <div class="photo photo-pool" role="img" aria-label="Modern home with turquoise swimming pool"></div>
  <div class="photo photo-steps" role="img" aria-label="Stone retaining wall with steps"></div>
  <div class="photo photo-firepit" role="img" aria-label="Lakeside patio with fire pit and lounge chairs at dusk"></div>

  <section class="services">
    <h2>OUR SERVICES</h2>
    <div class="service" style="left:77px;top:62px"><svg viewBox="0 0 32 32" fill="none" stroke="var(--navy)" stroke-width="2"><path d="M3 30V11L16 3l13 8v19"/><rect x="10" y="15" width="12" height="10"/></svg>Paver Patios</div>
    <div class="service" style="left:77px;top:111px"><svg viewBox="0 0 32 32" fill="none" stroke="var(--navy)" stroke-width="2"><path d="M3 30V11L16 3l13 8v19"/><path d="M8 24l5-8h6l5 8z" fill="var(--navy)"/></svg>Paver Driveways</div>
    <div class="service" style="left:77px;top:160px"><svg viewBox="0 0 32 32" fill="none" stroke="var(--navy)" stroke-width="2"><path d="M3 30V11L16 3l13 8v19"/><path d="M10 15h10M10 19h12M12 23h8"/></svg>Retaining Walls</div>
    <div class="service" style="left:280px;top:62px"><svg viewBox="0 0 32 32" fill="none" stroke="var(--navy)" stroke-width="2"><path d="M3 30V11L16 3l13 8v19"/><path d="M9 22q2-2 4 0t4 0 4 0M12 12v8M19 12v8M12 15h7"/></svg>Pools</div>
    <div class="service" style="left:280px;top:111px"><svg viewBox="0 0 32 32" fill="none" stroke="var(--navy)" stroke-width="2"><path d="M3 30V11L16 3l13 8v19"/><path d="M9 15h14M9 24h14M11 15v9M16 15v9M21 15v9"/></svg>Decks &amp; Railings</div>
    <div class="service" style="left:280px;top:160px"><svg viewBox="0 0 32 32" fill="none" stroke="var(--navy)" stroke-width="2"><path d="M3 30V11L16 3l13 8v19"/><path d="M9 19l7-6 7 6v6H9z" fill="var(--navy)"/></svg>Firepits &amp; Fireplaces</div>
    <div class="service" style="left:490px;top:62px"><svg viewBox="0 0 32 32" fill="none" stroke="var(--navy)" stroke-width="2"><path d="M3 30V11L16 3l13 8v19"/><path d="M13 13h6l-1 7h-4zM16 20v5"/></svg>Outdoor Lighting</div>
    <div class="service" style="left:490px;top:111px"><svg viewBox="0 0 32 32" fill="none" stroke="var(--navy)" stroke-width="2"><path d="M3 30V11L16 3l13 8v19"/><circle cx="16" cy="19" r="6"/><path d="M16 15v8M12 19h8"/></svg>And More...</div>
    <div class="seal" role="img" aria-label="Years of experience seal"></div>
  </section>

  <section class="contact">
    <h3>CONTACT US TODAY</h3>
    <div class="phone"><svg viewBox="0 0 48 48" fill="none" stroke="var(--gold)" stroke-width="4" stroke-linecap="round"><path d="M10 6l8 8-4 5c2 6 7 11 13 13l5-4 8 8-6 6C20 40 6 26 4 12z" fill="var(--gold)" stroke="none"/><path d="M28 10a10 10 0 0 1 10 10M28 3a17 17 0 0 1 17 17"/></svg>[206]-555-0148</div>
    <div class="email">info@summitstonebuilders.com</div>
  </section>
</div>
</body>
</html>
```